RTavenor Business Cards & Letterhead

I have a logo but need a design for some new business cards. We are a Design-Build Firm that specializes in the design and construction of commercial projects.
the cards need to be professional. no cartoon stuff.
i would like to have the cards in AI format so I can update the card as needed. Logo is provided.
Our Address is: 4187 Marlowe Ct. Apex, North Carolina 27614

```html
<!DOCTYPE html>
<html lang="en">
<head>
<meta charset="utf-8">
<title>RTavenor Letterhead and Business Cards</title>
<link href="https://fonts.googleapis.com/css2?family=Lato:wght@400;700&family=Open+Sans:wght@400;700&family=Great+Vibes&display=swap" rel="stylesheet">
<style>
  :root {
    --bg: #ebe8e4;
    --paper: #ffffff;
    --ink: #222222;
    --brand-grey: #6e6e70;
    --brand-blue: #1b67a6;
    --shadow: rgba(0, 0, 0, 0.18);
  }
  * { margin: 0; padding: 0; box-sizing: border-box; }
  html, body { width: 1200px; height: 942px; overflow: hidden; }
  body { background: var(--bg); position: relative; font-family: "Lato", sans-serif; color: var(--ink); }

  .letterhead {
    position: absolute; left: 84px; top: 89px; width: 541px; height: 765px;
    background: var(--paper); box-shadow: 0 2px 8px var(--shadow);
  }
  .wordmark { position: absolute; display: flex; align-items: center; font-family: "Open Sans", sans-serif; font-weight: 700; color: var(--brand-grey); letter-spacing: -0.5px; line-height: 1; }
  .wordmark .mark { background: var(--brand-blue); display: block; }
  .letterhead .wordmark { left: 27px; top: 57px; font-size: 33px; gap: 6px; }
  .letterhead .wordmark .mark { width: 24px; height: 24px; }

  .contact-block { position: absolute; border-left: 1.5px solid var(--brand-blue); font-family: "Open Sans", sans-serif; }
  .letterhead .contact-block { left: 388px; top: 38px; padding-left: 10px; font-size: 10px; line-height: 12px; height: 61px; }
  .contact-block .address { margin-bottom: 7px; }
  .contact-line { display: flex; align-items: center; gap: 3px; }
  .icon { width: 8px; height: 8px; fill: var(--brand-blue); flex: none; }

  .letter { position: absolute; left: 27px; width: 488px; font-size: 11.5px; line-height: 12.3px; }
  .letter p { text-align: justify; }
  .date { top: 176px; }
  .recipient { top: 202px; }
  .company { top: 240px; }
  .salutation { top: 295px; font-size: 14px; font-weight: 700; }
  .para-1 { top: 324px; }
  .para-2 { top: 384px; }
  .para-3 { top: 444px; }
  .para-4 { top: 491px; }
  .closing { top: 542px; }
  .signature { top: 612px; font-family: "Great Vibes", cursive; font-size: 26px; line-height: 30px; }

  .card {
    position: absolute; left: 673px; width: 444px; height: 255px;
    background: var(--paper); border-radius: 24px; box-shadow: 0 2px 8px var(--shadow);
  }
  .card-front { top: 201px; }
  .card-back { top: 488px; }
  .card-front .wordmark { left: 50%; top: 104px; transform: translateX(-50%); font-size: 58px; gap: 8px; }
  .card-front .wordmark .mark { width: 40px; height: 40px; }
  .card-back .wordmark { left: 34px; top: 112px; font-size: 29px; gap: 5px; }
  .card-back .wordmark .mark { width: 20px; height: 20px; }

  .card-back .contact-block { left: 259px; top: 55px; height: 144px; padding-left: 11px; font-size: 13px; line-height: 16px; }
  .holder-name { font-size: 18px; line-height: 20px; font-weight: 700; color: var(--brand-blue); }
  .holder-role { margin-bottom: 14px; }
  .card-back .contact-line { gap: 4px; }
  .card-back .icon { width: 10px; height: 10px; }
  .card-back .address { margin-top: 14px; margin-bottom: 0; }
</style>
</head>
<body>

<svg width="0" height="0" style="position:absolute" aria-hidden="true">
  <symbol id="icon-phone" viewBox="0 0 10 10"><path d="M2.2 0.6l1.5 1.8-0.9 1.1c0.5 1.2 1.4 2.1 2.6 2.6l1.1-0.9 1.8 1.5-0.9 1.8C4.5 8.3 1.7 5.5 0.4 1.5z"/></symbol>
  <symbol id="icon-mail" viewBox="0 0 10 10"><path d="M0.5 2.5h9v5h-9z M0.5 2.5l4.5 3 4.5-3" /></symbol>
  <symbol id="icon-globe" viewBox="0 0 10 10"><circle cx="5" cy="5" r="4.5"/><path d="M5 0.5v9M0.5 5h9" stroke="#fff" stroke-width="0.8" fill="none"/></symbol>
</svg>

<section class="letterhead">
  <div class="wordmark"><span class="mark"></span>RTavenor</div>

  <div class="contact-block">
    <div class="address">4187 Marlowe Ct. Apex,<br>North Carolina 27614</div>
    <div class="contact-line"><svg class="icon"><use href="#icon-phone"/></svg>123 456 789</div>
    <div class="contact-line"><svg class="icon"><use href="#icon-mail"/></svg>info@yourmail.com</div>
    <div class="contact-line"><svg class="icon"><use href="#icon-globe"/></svg>www.yourwebsite.com</div>
  </div>

  <div class="letter date">January-03-2020</div>
  <div class="letter recipient">Mr, Evan Marsh<br>President</div>
  <div class="letter company">Harbor Corporation<br>123 Street Name, Suite# 10<br>City, State, 120023</div>
  <div class="letter salutation">Dear Mr, Evan</div>
  <p class="letter para-1">Lorem ipsum dolor sit amet, consectetur adipiscing elit, sed do eiusmod tempor incididunt ut labore et dolore magna aliqua. Ut enim ad minim veniam, quis nostrud exercitation ullamco laboris nisi ut aliquip ex ea commodo consequat. Duis aute irure dolor in reprehenderit in voluptate velit esse cillum dolore eu fugiat nulla pariatur.</p>
  <p class="letter para-2">Lorem ipsum dolor sit amet, consectetur adipiscing elit, sed do eiusmod tempor incididunt ut labore et dolore magna aliqua. Ut enim ad minim veniam, quis nostrud exercitation ullamco laboris nisi ut aliquip ex ea commodo consequat. Duis aute irure dolor in reprehenderit in voluptate velit esse cillum dolore eu fugiat nulla pariatur.</p>
  <p class="letter para-3">Lorem ipsum dolor sit amet, consectetur adipiscing elit, sed do eiusmod tempor incididunt ut labore et dolore magna aliqua. Ut enim ad minim veniam, quis nostrud exercitation ullamco laboris nisi ut aliquip ex ea commodo consequat.</p>
  <p class="letter para-4">Excepteur sint occaecat cupidatat non proident, sunt in culpa qui officia deserunt mollit anim id est laborum. re et dolore magnam aliquam quaerat voluptatem.</p>
  <div class="letter closing">Regards</div>
  <div class="letter signature">Colin Ashby</div>
</section>

<section class="card card-front">
  <div class="wordmark"><span class="mark"></span>RTavenor</div>
</section>

<section class="card card-back">
  <div class="wordmark"><span class="mark"></span>RTavenor</div>
  <div class="contact-block">
    <div class="holder-name">NADIA FERRELL</div>
    <div class="holder-role">Managing Director</div>
    <div class="contact-line"><svg class="icon"><use href="#icon-phone"/></svg>123 456 789</div>
    <div class="contact-line"><svg class="icon"><use href="#icon-mail"/></svg>info@yourmail.com</div>
    <div class="contact-line"><svg class="icon"><use href="#icon-globe"/></svg>www.yourwebsite.com</div>
    <div class="address">4187 Marlowe Ct. Apex,<br>North Carolina 27614</div>
  </div>
</section>

</body>
</html>
```